Brightwave Reach - Business Card

We need a business card for a Social Media Marketing company that specializes in online marketing for small businesses in Canada using common Social Media platforms such as Pixlora, Chatterly, Blinkpost & Quibber.

I have uploaded a copy of our logo which I would like utilized in the business card. We would like the business card to be modern yet classy design.

Our website is www.brightwavereach.ca

Industry/Entity Type

Marketing

Contact Information for Business Card

Email: info@brightwavereach.ca
Website: www.brightwavereach.ca
Telephone: 604-555-0193

Colors

Designer to choose colors to be used in the design.

Requirements
Must have
• Social Media icons on reverse
• Please add some designs with color.

```html
<!DOCTYPE html>
<html lang="en">
<head>
<meta charset="utf-8">
<title>Brightwave Reach - Business Card</title>
<link rel="stylesheet" href="https://fonts.googleapis.com/css2?family=Roboto:wght@400;500&family=Roboto+Condensed:wght@700&display=swap">
<style>
  :root {
    --stage: #2b2b2b;
    --paper: #f1f1f0;
    --ink: #3b3d3f;
    --ink-soft: #9a9a9a;
    --frame: #4a4a4a;
    --card-dark: #3a3d40;
    --on-dark: #f2f2f2;
    --rule-dark: #8b8e91;
  }
  * { margin: 0; padding: 0; box-sizing: border-box; }
  html, body { width: 1200px; height: 960px; overflow: hidden; }
  body { background: var(--stage); position: relative; font-family: "Roboto", Arial, sans-serif; }

  .card { position: absolute; width: 600px; height: 342px; box-shadow: 0 4px 10px rgba(0,0,0,.45); }
  .card--front { left: 314px; top: 113px; background: var(--paper); }
  .card--back { left: 311px; top: 472px; background: var(--card-dark); }

  .frame-outer { position: absolute; left: 16px; top: 12px; right: 16px; bottom: 12px; border: 3px solid var(--frame); }
  .frame-inner { position: absolute; left: 21px; top: 17px; right: 21px; bottom: 17px; border: 1px solid var(--frame); }

  .brand-name {
    position: absolute; font-family: "Roboto Condensed", "Arial Narrow", sans-serif; font-weight: 700;
    text-transform: uppercase; text-align: center; line-height: 1; letter-spacing: .5px;
  }
  .card--front .brand-name { left: 86px; top: 134px; width: 188px; font-size: 29px; color: var(--ink); }
  .card--back .brand-name { left: 190px; top: 120px; width: 220px; font-size: 34px; color: var(--on-dark); }

  .divider { position: absolute; left: 306px; top: 97px; width: 1px; height: 150px; background: #c9c9c9; }

  .person { position: absolute; left: 343px; top: 110px; }
  .person__name { font-family: "Roboto Condensed", "Arial Narrow", sans-serif; font-weight: 700; font-size: 21px; color: var(--ink); }
  .person__role { font-size: 15px; color: var(--ink-soft); margin-top: 3px; }

  .contact { position: absolute; left: 343px; top: 175px; list-style: none; }
  .contact li { display: flex; align-items: center; font-size: 14.5px; color: var(--ink); height: 19.5px; }
  .contact svg { width: 12px; height: 12px; margin-right: 9px; fill: var(--ink); }

  .social { position: absolute; left: 120px; top: 286px; width: 360px; display: flex; align-items: center; }
  .social__rule { flex: 1; height: 1px; background: linear-gradient(90deg, transparent, var(--rule-dark)); }
  .social__rule--right { background: linear-gradient(90deg, var(--rule-dark), transparent); }
  .social__list { display: flex; gap: 10px; padding: 0 10px; list-style: none; }
  .social__list li { font-size: 11px; color: var(--on-dark); letter-spacing: .3px; }
</style>
</head>
<body>
  <section class="card card--front" aria-label="Card front">
    <div class="frame-outer"></div>
    <div class="frame-inner"></div>
    <div class="brand-name">Brightwave<br>Reach</div>
    <div class="divider"></div>
    <div class="person">
      <div class="person__name">DANIEL HART</div>
      <div class="person__role">CEO/FOUNDER</div>
    </div>
    <ul class="contact">
      <li><svg viewBox="0 0 24 24"><path d="M6.6 10.8a15.1 15.1 0 0 0 6.6 6.6l2.2-2.2a1 1 0 0 1 1-.25 11.4 11.4 0 0 0 3.6.57 1 1 0 0 1 1 1V20a1 1 0 0 1-1 1A17 17 0 0 1 3 4a1 1 0 0 1 1-1h3.5a1 1 0 0 1 1 1c0 1.25.2 2.45.57 3.57a1 1 0 0 1-.25 1z"/></svg>604-555-0193</li>
      <li><svg viewBox="0 0 24 24"><path d="M2 5h20v2l-10 6L2 7z M2 9l10 6 10-6v10H2z"/></svg>info@brightwavereach.ca</li>
      <li><svg viewBox="0 0 24 24"><circle cx="12" cy="12" r="10"/><path d="M2 12h20M12 2c3 3 3 17 0 20M12 2c-3 3-3 17 0 20" stroke="#f1f1f0" stroke-width="1.5" fill="none"/></svg>www.brightwavereach.ca</li>
    </ul>
  </section>

  <section class="card card--back" aria-label="Card back">
    <div class="brand-name">Brightwave<br>Reach</div>
    <div class="social">
      <span class="social__rule"></span>
      <ul class="social__list">
        <li>Chatterly</li>
        <li>Pixlora</li>
        <li>Quibber</li>
      </ul>
      <span class="social__rule social__rule--right"></span>
    </div>
  </section>
</body>
</html>
```